Brightfen Business Card Redesign & Logo Update

We need to update our business cards to something more modern and fresh. Brightfen can provide the current color schemes and old design examples, but welcome creativity in helping us with this redesign. PLEASE NOTE that we no longer utilize the "tree" and/or "leaf" imagery in our branding. If able would apprecaite an update on the quality of our "words only" logo in Ai. / PNG formats too.

Target Market(s)

Investors, landowners, corporate partners, contractors

Industry/Entity Type

Environmental Restoration & Conservation

Contact Information for Business Card

Logo, persons name, title, mailing address, phone and email, website url

Font styles to use
Other font styles liked:
• Merriweather

Requirements
Nice to have
• Logo, persons name, title, mailing address, phone and email, website url, but open to ideams
Should not have
• No all back backgrounds

```html
<!DOCTYPE html>
<html lang="en">
<head>
<meta charset="utf-8">
<title>Brightfen Business Card</title>
<link rel="stylesheet" href="https://fonts.googleapis.com/css2?family=Open+Sans:wght@400;600;700;800&display=swap">
<style>
  :root {
    --stage: #5e6261;
    --card: #2e3b34;
    --card-deep: #26322c;
    --edge: #e8791e;
    --orange: #ef7d1a;
    --green: #3fae5f;
    --ink: #f2f2f2;
    --muted: #c9d2cc;
    --gloss: #a9b3ad;
  }
  * { margin: 0; padding: 0; box-sizing: border-box; }
  html, body { width: 1200px; height: 801px; overflow: hidden; }
  body {
    background: var(--stage);
    font-family: "Open Sans", sans-serif;
    position: relative;
  }
  .card {
    position: absolute;
    top: 245px;
    width: 530px;
    height: 310px;
    background: linear-gradient(160deg, var(--card) 0%, var(--card-deep) 100%);
    border: 1.5px solid var(--edge);
    border-radius: 18px;
    overflow: hidden;
  }
  .card--front { left: 50px; }
  .card--back { left: 620px; }

  .brand {
    position: absolute;
    text-align: right;
  }
  .brand__name {
    font-family: "Open Sans", sans-serif;
    font-weight: 800;
    color: var(--orange);
    letter-spacing: 1px;
    text-transform: uppercase;
    line-height: 1;
  }
  .brand__tagline {
    font-weight: 700;
    text-transform: uppercase;
    letter-spacing: 0.5px;
    color: var(--ink);
    line-height: 1.2;
  }
  .card--front .brand { top: 36px; right: 40px; }
  .card--front .brand__name { font-size: 34px; }
  .card--front .brand__tagline { font-size: 10px; margin-top: 4px; }

  .contact {
    position: absolute;
    top: 118px;
    right: 40px;
    width: 240px;
    color: var(--ink);
    font-size: 13.5px;
    line-height: 1.45;
  }
  .contact__address { margin-bottom: 14px; }
  .contact__line {
    display: flex;
    align-items: center;
    gap: 8px;
  }
  .contact__line svg { width: 12px; height: 12px; flex: none; }

  .holder {
    position: absolute;
    left: 40px;
    bottom: 52px;
  }
  .holder__name {
    color: var(--orange);
    font-weight: 700;
    font-size: 19px;
    letter-spacing: 1px;
    text-transform: uppercase;
  }
  .holder__title {
    color: var(--ink);
    font-size: 15px;
  }
  .side-tab {
    position: absolute;
    left: -6px;
    bottom: 40px;
    width: 16px;
    height: 26px;
    background: var(--orange);
    border-radius: 5px;
  }

  .card--back .brand { top: 112px; right: 50px; }
  .card--back .brand__name {
    font-size: 60px;
    color: var(--gloss);
    letter-spacing: 3px;
  }
  .card--back .brand__tagline {
    font-size: 15px;
    color: var(--gloss);
    margin-top: 6px;
    letter-spacing: 1px;
  }
</style>
</head>
<body>
  <section class="card card--front">
    <div class="brand">
      <p class="brand__name">Brightfen</p>
      <p class="brand__tagline">Environmental Credit Company</p>
    </div>
    <div class="contact">
      <p class="contact__address">1408 Marlow Cove Rd<br>Seabrook CA 90412</p>
      <p class="contact__line">
        <svg viewBox="0 0 12 12" aria-hidden="true"><path fill="#3fae5f" d="M2.5 1l2 2.2-1 1.2a6 6 0 0 0 4 4l1.2-1 2.3 2-1.3 1.6C5.5 11 1 6.5 1 2.3z"/></svg>
        555-014-2278
      </p>
      <p class="contact__line">
        <svg viewBox="0 0 12 12" aria-hidden="true"><rect x="1" y="2.5" width="10" height="7" fill="#3fae5f"/><path d="M1 2.5l5 4 5-4" fill="none" stroke="#2e3b34" stroke-width="1"/></svg>
        dkellner@brightfen.com
      </p>
      <p class="contact__line">
        <svg viewBox="0 0 12 12" aria-hidden="true"><circle cx="6" cy="6" r="5" fill="none" stroke="#3fae5f" stroke-width="1.4"/><path d="M1 6h10M6 1c-2.5 3-2.5 7 0 10M6 1c2.5 3 2.5 7 0 10" fill="none" stroke="#3fae5f" stroke-width="1"/></svg>
        www.brightfen.com
      </p>
    </div>
    <div class="side-tab"></div>
    <div class="holder">
      <p class="holder__name">Dana Kellner</p>
      <p class="holder__title">President</p>
    </div>
  </section>

  <section class="card card--back">
    <div class="brand">
      <p class="brand__name">Brightfen</p>
      <p class="brand__tagline">Environmental Credit Company</p>
    </div>
  </section>
</body>
</html>
```